Martial Arts Website

Redevelopment of existing martial arts website.

The academy teaches traditional shaolin martial arts, including Shaolin Kung Fu, Wu Shu, Tai Chi, Qigong and Wing Chun and the site needs to reflect the traditional roots (eg, no tacky boxing imagery)

Existing website is www.copperlantern.com.au to get a feel for the desired color scheme (black, green and red). The exact colors can be tweaked though. Please only reuse the logo and font (Karate) - there isnt anything else from the current design that needs to remain.

The current website includes links to a ClipHarbor channel that includes demonstrations of the training conducted to better guide the design.

The new website site map will be:
1. Home
2. Programs - summary page describing each form of training
a. Tiny Otters
b. Kids Kung Fu
c. Youth Kung Fu
d. Adults Kung Fu
e. Wing Chun
f. Tai Chi & Qigong
g. Weaponry Classes
h. 72 Arts of Shaolin Conditioning Program
i. Acrobatics and Wu Shu
j. Fitness Boxing
3. Timetable
4. Coaches - summary page describing all coaches
a. Sifu (Master)
b. Sihing Kit
c. Sihing Sam
d. Sihing Marcus
X. ... up to 10 or so coaches
5. Member Zone
6. Contact Us
Updates

Logo now attached to brief - sorry I only have it in PDF

Just to clarify, I am only expecting a PSD design - no HTML required

Reason: Thanks for the designs, we love a lot of them just require a little extra time to tweak the designs and establish the potential. Thanks for your understanding and efforts.

Target Market(s)

Parents, teenagers, young adults, adults, elderly

Industry/Entity Type

Training

Requirements
Must have
• Chinese kung fu dragon imagery throughout the background
Links to Chatterly and ClipHarbor channel
Promo/icon in the header "Try 2 free classes now"
Home page should include an embedded ClipHarbor video

```html
<!DOCTYPE html>
<html lang="en">
<head>
<meta charset="utf-8">
<title>Copper Lantern Martial Arts Academy</title>
<link rel="stylesheet" href="https://fonts.googleapis.com/css2?family=Signika:wght@400;600&family=Source+Sans+3:wght@400;600&display=swap">
<style>
:root{
  --bg-green:#1f6a12;
  --bg-green-dark:#123f0a;
  --frame:#0a1a06;
  --panel:#000;
  --sidebar:#0c1e08;
  --nav-top:#2f9a1c;
  --nav-bot:#1a7010;
  --tab:#0c3a07;
  --accent:#3ed01e;
  --accent-soft:#6ad24a;
  --nav-text:#0b2306;
  --text:#f2f2f2;
  --muted:#bdbdbd;
  --table:#1a8a10;
  --table-line:#2fa022;
}
*{margin:0;padding:0;box-sizing:border-box}
html,body{width:845px;height:1200px;overflow:hidden}
body{position:relative;background:linear-gradient(180deg,var(--bg-green) 0,var(--bg-green-dark) 560px,#0b2a06 590px,var(--bg-green-dark) 630px,var(--bg-green) 1000px);font-family:"Source Sans 3",sans-serif;color:var(--text)}
.site-frame{position:absolute;left:12px;top:88px;width:820px;height:928px;background:var(--frame);border-radius:4px}
.main-nav{position:absolute;left:21px;top:95px;width:801px;height:53px;background:linear-gradient(180deg,var(--nav-top),var(--nav-bot));border-radius:3px}
.main-nav a{position:absolute;top:22px;font-family:"Signika",sans-serif;font-size:12px;color:var(--nav-text);text-decoration:none;letter-spacing:.2px}
.main-nav .active-tab{position:absolute;left:94px;top:8px;width:95px;height:45px;background:var(--tab);border-radius:6px 6px 0 0}
.main-nav a.active{color:var(--accent)}
.dropdown{position:absolute;left:115px;top:148px;width:214px;height:104px;background:var(--tab);border-radius:0 0 6px 6px;z-index:3}
.dropdown a{position:absolute;font-family:"Signika",sans-serif;font-size:10px;color:var(--accent-soft);text-decoration:none}
.hero{position:absolute;left:22px;top:151px;width:799px;height:297px;background:linear-gradient(160deg,#c9c2b8 0%,#e7e2dc 35%,#b98f7a 75%,#9d6f5a 100%)}
.brand-badge{position:absolute;left:330px;top:18px;width:146px;height:146px;border-radius:50%;background:#060606;border:6px solid var(--accent);display:flex;align-items:center;justify-content:center;text-align:center;z-index:4}
.brand-badge span{font-family:"Source Sans 3",sans-serif;font-weight:600;font-size:15px;color:var(--accent-soft);line-height:1.2}
.content{position:absolute;left:22px;top:450px;width:556px;height:562px;background:var(--panel)}
.welcome-title,.section-title,.side-title{font-family:"Signika",sans-serif;font-weight:400;color:var(--accent)}
.welcome-title{position:absolute;left:16px;top:18px;font-size:14px}
.intro{position:absolute;left:16px;top:42px;width:518px;font-size:9.6px;line-height:14.8px;text-align:justify}
.intro p+p{margin-top:4px}
.program{position:absolute;left:16px;width:520px;font-size:8.6px;line-height:14.5px}
.program b{font-family:"Signika",sans-serif;font-weight:400;font-size:11px;color:var(--accent)}
.section-title{position:absolute;left:14px;top:370px;font-size:14px}
.classes{position:absolute;left:12px;top:395px;width:540px;height:153px;background:var(--table);border-radius:3px;border-collapse:collapse}
.classes td{border:1px solid var(--table-line);padding:0 0 0 25px;font-size:10.3px;line-height:14.8px;height:51px;color:#fff}
.classes tr:first-child td{border-top:none}.classes tr:last-child td{border-bottom:none}
.classes td:first-child{border-left:none;width:142px}.classes td:last-child{border-right:none;padding-left:25px}
.classes td:nth-child(2){width:144px;padding-left:30px}
.sidebar{position:absolute;left:587px;top:452px;width:228px;height:548px;background:var(--sidebar);border-radius:4px}
.news{position:absolute;left:16px;top:16px;width:200px}
.side-title{font-size:14px}
.news-item{margin-top:10px}
.news-item .date{font-size:8.8px;font-weight:600;color:#fff}
.news-item p{margin-top:5px;font-size:8.6px;line-height:14.8px;color:var(--accent)}
.box{position:absolute;left:9px;width:212px;background:#000;border-radius:6px;padding:12px}
.signup{top:278px;height:92px}
.email-field{margin-top:10px;position:relative;width:194px;height:24px;border-radius:12px;background:linear-gradient(180deg,#2faa1c,#157a0c);padding-left:13px;font-size:9px;font-style:italic;line-height:24px;color:#0b3206}
.email-go{position:absolute;right:-2px;top:-3px;width:30px;height:30px;border-radius:50%;background:#000;border:1.5px solid var(--accent);color:#fff;font-size:12px;font-style:normal;text-align:center;line-height:27px}
.social{top:376px;height:92px}
.social-links{margin-top:12px;display:flex;gap:14px;font-size:10px;color:#fff}
.site-footer{position:absolute;left:0;top:1016px;width:845px;height:184px;background:#000}
.footer-col{position:absolute;top:22px;list-style:none}
.footer-col li{font-size:9.6px;line-height:25px;color:#e8e8e8;padding-left:14px;position:relative}
.footer-col li::before{content:"";position:absolute;left:0;top:9px;border-left:4px solid #9a9a9a;border-top:3px solid transparent;border-bottom:3px solid transparent}
.footer-badge{position:absolute;left:647px;top:13px;width:100px;height:100px;border-radius:50%;background:#060606;border:4px solid var(--accent);display:flex;align-items:center;justify-content:center;text-align:center}
.footer-badge span{font-weight:600;font-size:11px;color:var(--accent-soft);line-height:1.2}
.copyright{position:absolute;left:39px;top:149px;font-size:9.4px;color:#8a8a8a}
</style>
</head>
<body>
<div class="site-frame"></div>

<nav class="main-nav">
  <div class="active-tab"></div>
  <a style="left:42px">HOME</a>
  <a class="active" style="left:110px">PROGRAMS</a>
  <a style="left:205px">TIMETABLE</a>
  <a style="left:501px">COACHES</a>
  <a style="left:575px">MEMBER ZONE</a>
  <a style="left:679px">CONTACT US</a>
</nav>

<div class="hero" role="img" aria-label="Photo of a master leading a tai chi class of students in white uniforms in a sports hall"></div>

<div class="dropdown">
  <a style="left:18px;top:11px">Tiny Otters</a>
  <a style="left:110px;top:11px">Wing Chun</a>
  <a style="left:18px;top:33px">Kids Kung Fu</a>
  <a style="left:110px;top:33px">Tai Chi &amp; Qigong</a>
  <a style="left:18px;top:55px">Youth Kung Fu</a>
  <a style="left:110px;top:55px">Weaponry Classes</a>
  <a style="left:18px;top:77px">Adults Kung Fu</a>
  <a style="left:110px;top:77px">72 Arts of Shaolin</a>
</div>

<div class="brand-badge"><span>Copper<br>Lantern</span></div>

<main class="content">
  <h1 class="welcome-title">Welcome to Copper Lantern Martial Arts Academy - NSW Australia</h1>
  <div class="intro">
    <p>Lorem ipsum dolor sit amet, consectetuer adipiscing elit. Nam cursus. Morbi ut mi. Nullam enim leo, egestas id, condimentum at, laoreet mattis, massa. Sed eleifend nonummy diam. Praesent mauris ante, elementum et, bibendum at, posuere sit amet, nibh. Duis tincidunt lectus quis dui viverra vestibulum.</p>
    <p>Suspendisse vulputate aliquam dui. Nulla elementum dui ut augue. Aliquam vehicula mi at mauris. Maecenas placerat, nisl at consequat rhoncus, sem nunc gravida justo, quis eleifend arcu velit quis lacus. Morbi magna magna, tincidunt a, mattis non, imperdiet vitae, tellus. Sed odio est, auctor ac, sollicitudin in, consequat vitae, orci. Fusce id felis. Vivamus sollicitudin metus eget eros.</p>
  </div>
  <p class="program" style="top:164px"><b>Tiny Otters</b> – ages 4 to 6. A specialised martial arts program for ages 4 to 6.</p>
  <p class="program" style="top:191px"><b>Kids Kung Fu</b> – ages 6 to 11. Practical, Responsible Instruction. Plus, we specialize in powerful character development skills in a positive environment. Kids learn self defence NOT fighting, anti bullying techniques.</p>
  <p class="program" style="top:233px"><b>Youth Kung Fu</b> – ages 11 to 15. The ultimate way to Build Confidence, Self-Esteem, Self-Discipline, and Athletic Skills, while learning self defence in a tradition style Martial Arts.</p>
  <p class="program" style="top:275px"><b>Adults Shaolin Kung Fu</b> - ages 15 &amp; over. Self defence utilizing great range of punches, kicks, joint-locking, throwing and grappling techniques. The class utilizes traditional training methods designed to develop a sound mind and body.</p>
  <p class="program" style="top:317px"><b>Wing Chun Kung Fu</b> – ages 13 &amp; over. Authentic Wing Chun Kung Fu by Harbour Wing Chun in the direct lineage to Lo Wen (World famous Wing Chun Master). Effective, direct, efficient Self Defence.</p>

  <h2 class="section-title">Our Classes</h2>
  <table class="classes">
    <tr><td>Tiny Otters<br>Ages 4 to 6</td><td>Adults Kung Fu<br>Ages 15 &amp; over</td><td>Weaponry Classes<br>Ages 5 &amp; over</td></tr>
    <tr><td>Kids Kung Fu<br>Ages 6 to 11</td><td>Wing Chun<br>Ages 13 &amp; over</td><td>72 Arts of Shaolin<br>Conditioning Program</td></tr>
    <tr><td>Youth Kung Fu<br>Ages 11 to 15</td><td>Tai Chi &amp; Qigong<br>All ages</td><td>Performance Team<br>Acrobatics &amp; Wu Shu</td></tr>
  </table>
</main>

<aside class="sidebar">
  <section class="news">
    <h2 class="side-title">News &amp; Updates</h2>
    <div class="news-item"><div class="date">18.2012.2012</div><p>Lorem ipsum dolor sit amet, consectetuer adipiscing elit. Nam cursus. Morbi ut mi. Nullam enim leo, egestas id.</p></div>
    <div class="news-item"><div class="date">18.2012.2012</div><p>Lorem ipsum dolor sit amet, consectetuer adipiscing elit. Nam cursus. Morbi ut mi. Nullam enim leo, egestas id.</p></div>
    <div class="news-item"><div class="date">18.2012.2012</div><p>Lorem ipsum dolor sit amet, consectetuer adipiscing elit. Nam cursus. Morbi ut mi. Nullam enim leo, egestas id.</p></div>
  </section>
  <section class="box signup">
    <h2 class="side-title">Newsletters Sign Up</h2>
    <div class="email-field">type email address<span class="email-go">Go</span></div>
  </section>
  <section class="box social">
    <h2 class="side-title">Social Media</h2>
    <div class="social-links"><span>ClipHarbor</span><span>Chatterly</span></div>
  </section>
</aside>

<footer class="site-footer">
  <ul class="footer-col" style="left:39px"><li>Home</li><li>Programs</li><li>Timtable</li><li>Coaches</li></ul>
  <ul class="footer-col" style="left:139px"><li>Support</li><li>FAQ</li><li>Newsletes</li><li>Social Media</li></ul>
  <ul class="footer-col" style="left:249px"><li>Tiny Otters</li><li>Kids Kung Fu</li><li>Youth Kung Fu</li><li>Adults Kung Fu</li></ul>
  <ul class="footer-col" style="left:377px"><li>Wing Chun</li><li>Tai Chi &amp; Qigong</li><li>Weaponry Classes</li><li>72 Arts of Shaolin</li></ul>
  <div class="footer-badge"><span>Copper<br>Lantern</span></div>
  <p class="copyright">© 2012 Company Name &nbsp;|&nbsp; All right reserved</p>
</footer>
</body>
</html>
```